A website where experts collaborate on your project

I am building a new website where experts (yes, like designers) collaborate on projects with the project owner. More minds = more collaboration = better end product. Please see Pelmora(dot)com for a quick landing page I created for collaborating on presentations (although there will be many project types offered)

I am looking for a DESIGNER LONG TERM, but for now, just need initial mock ups to show the web programmers.

I have 21 Word documents loosely designed, what I would like to see here is a theme. Please DO NOT GO OFF WHAT YOU CURRENTLY SEE AT PELMORA. What is up now is only a quick landing page.

You can view a Word doc of the homepage here:
https://www.filevanta.com/s/qx83kdm2/home.docx?dl=0

WHAT AM I LOOKING FOR?
A clean, well designed theme.

Here is a link to the logo:
https://www.filevanta.com/s/mr47tpz9/logo%20-%20horizontal.tif?dl=0
-----------------------------------------
Here are a few sites I like the design of and what I like about them:
www.quenbrook.com-all around my favorite, beautiful graphics, clean layout, bold use of colors on a dark background
Ravelto.com- clean layout, The use of humans and bubble style elements.
Mintharbor.com :) clean, bold, unique pop art style but professional
plumevault.com - From the unique colors and artwork and the ability of that art to not interfere with the important elements of the site
sparkwidgets.com-clean, nice colors, well organized and separated sections.
www.dunmereco.com-love the font, use of colors and sectionalized style

All in all, I am not picky and open to so many styles. I would ultimately like the designer I pick to design all 21 pages.
Updates

Hello everyone,Moving forward, I would like you all to pay special attention to the section in my brief titled "Here are a few sites I like the design of and what I like about them". Please see below, I handpicked each one of these as sites I really like. Thank you.Here are a few sites I like the design of and what I like about them:Ravelto.com- clean layout, The use of humans and bubble style elements.Mintharbor.com :) clean, bold, unique pop art style but professionalwriteraccess.com - From the unique colors and artwork and the ability of that art to not interfere with the important elements of the sitegrowthgeeks.com-clean, nice colors, well organized and separated sections.www.dunmereco.com-love the font, use of colors and sectionalized stylewww.quenbrook.com-beautiful graphics, clean layout, bold use of colors----------------------------------------- Added Tuesday, November 24, 2015

I updated the homepage, you can see it here:https://www.dropbox.com/s/kwlkbsookq3cg2m/1new%20homepage.docx?dl=0I am modeling it after my favorite designed site: triplelift.comI love the dark colors with the orange glowing style boldness of the buttons. It's real clean too. Added Tuesday, November 24, 2015

Target Market(s)

small business owners, marketers, freelancer writers, graphic designers,

Industry/Entity Type

Building

Number of Pages Required

5+ page

Requirements
Must have
• I can't think of anything the project must have.
Nice to have
• WHAT AM I LOOKING FOR?
• A clean, well designed theme. I had a designer do a bit of work putting elements together, I found it to be very plain, but I like the Application Page (https://www.filevanta.com/s/jb19ckr3/Pelmora-Website.ai?dl=0)
• Here is a link to the logo:
• https://www.filevanta.com/s/mr47tpz9/logo%20-%20horizontal.tif?dl=0
• Here are a few sites I like the design of and what I like about them:
• Ravelto.com- clean layout, The use of humans and bubble style elements.
• Mintharbor.com :) clean, bold, unique pop art style but professional
• plumevault.com - From the unique colors and artwork and the ability of that art to not interfere with the important elements of the site
• sparkwidgets.com-clean, nice colors, well organized and separated sections.
• www.dunmereco.com-love the font, use of colors and sectionalized style
• www.quenbrook.com-beautiful graphics, clean layout, bold use of colors
• -----------------------------------------
Should not have
• out of the boxed, templated style website. I want this site to be memorable and not look like a thousand others

```html
<!DOCTYPE html>
<html lang="en">
<head>
<meta charset="utf-8">
<title>Pelmora – The Evolution Of Feedback</title>
<link href="https://fonts.googleapis.com/css2?family=Open+Sans:wght@300;400;600&display=swap" rel="stylesheet">
<style>
:root{
  --teal:#3cc3bb;
  --orange:#f7941d;
  --ink:#2b2b33;
  --muted:#6f6f76;
  --sand:#f2efeb;
  --plum:#463f63;
  --night:#1d1f3a;
  --footer:#232323;
  --white:#ffffff;
}
*{margin:0;padding:0;box-sizing:border-box}
html,body{width:1200px;height:2922px;overflow:hidden}
body{font-family:"Open Sans",Arial,sans-serif;color:var(--ink);background:var(--white);position:relative}
.abs{position:absolute}
.teal{color:var(--teal)}
.orange{color:var(--orange)}

/* Hero */
.hero{position:absolute;left:0;top:0;width:1200px;height:577px;overflow:hidden}
.hero-photo{position:absolute;inset:0;background:
  radial-gradient(ellipse 700px 120px at 600px 450px,rgba(230,140,50,.55),transparent 70%),
  linear-gradient(180deg,#2b3470 0%,#3e5592 30%,#5a6fa3 52%,#20243f 70%,#0e0f1c 100%)}
.brand{left:82px;top:58px}
.brand-name{font-size:30px;font-weight:600;color:var(--orange);letter-spacing:-.5px;line-height:40px}
.menu{left:1090px;top:48px;width:30px}
.menu span{display:block;height:3px;background:var(--white);margin-bottom:6px}
.hero-title{left:0;top:182px;width:1200px;text-align:center;font-size:54px;font-weight:300;color:var(--white)}
.hero-sub{left:250px;top:266px;width:700px;text-align:center;font-size:21px;line-height:36px;font-weight:300;color:var(--teal);text-transform:uppercase}
.btn-ghost{top:362px;height:49px;border:2px solid rgba(255,255,255,.55);background:rgba(20,22,40,.55);color:var(--white);font-size:19px;display:flex;align-items:center;justify-content:center;border-radius:3px;text-transform:uppercase}
.scroll-cue{left:575px;top:475px}

/* How it works */
.how{position:absolute;left:0;top:577px;width:1200px;height:438px;background:var(--sand);clip-path:polygon(0 0,100% 0,100% 364px,50% 438px,0 364px)}
.section-title{position:absolute;left:0;width:1200px;text-align:center;font-weight:300;font-size:41px}
.how .section-title{top:22px}
.how-sub{top:95px;left:0;width:1200px;text-align:center;font-size:15px;color:#4a4a52;text-transform:uppercase}
.step{top:140px;width:320px;text-align:center}
.step-art{width:170px;height:160px;margin:0 auto;border-radius:8px;background:linear-gradient(135deg,#ecd9c4,#cfe6e4)}
.step-label{margin-top:20px;font-size:20px;color:var(--ink)}

/* Why */
.why-title{left:82px;top:1058px;font-size:42px;font-weight:300}
.why-copy{left:82px;top:1140px;width:490px;font-size:14px;line-height:27px;color:#444}
.why-list{left:82px;top:1266px;width:490px;list-style:none;font-size:14px;line-height:27px;color:#444}
.why-list li{position:relative;padding-left:16px}
.why-list li::before{content:"";position:absolute;left:0;top:10px;width:8px;height:8px;border-radius:50%;background:var(--teal)}
.btn-outline{left:82px;top:1426px;width:180px;height:50px;border:2px solid var(--orange);border-radius:4px;font-size:18px;color:var(--ink);display:flex;align-items:center;justify-content:center}
.devices-art{left:610px;top:1145px;width:520px;height:312px;border-radius:10px;background:linear-gradient(135deg,#dfe7ee,#9fd3d0 60%,#f6c98e)}

/* Project types */
.projects{position:absolute;left:0;top:1529px;width:1200px;height:384px;background:linear-gradient(135deg,#4d4670,var(--plum) 60%,#3e3858)}
.proj-col{position:absolute;top:40px}
.proj-col h3{font-size:28px;font-weight:300;color:var(--orange);padding-bottom:8px;border-bottom:2px dotted var(--orange)}
.proj-col ul{list-style:none;margin-top:14px}
.proj-col li{font-size:14px;line-height:35.5px;color:#ece9f3;padding-left:20px;position:relative;white-space:nowrap}
.proj-col li::before{content:"";position:absolute;left:2px;top:14px;width:6px;height:6px;border-top:2px solid var(--orange);border-right:2px solid var(--orange);transform:rotate(45deg)}

/* What we do */
.what .section-title{top:1955px}
.what-copy{left:100px;top:2026px;width:1000px;text-align:center;font-size:16px;line-height:28px;color:var(--muted);text-transform:uppercase}
.tablet{left:253px;top:2119px;width:696px;height:474px;background:#1b1b1d;border-radius:22px}
.tablet-screen{left:17px;top:24px;width:662px;height:428px;background:linear-gradient(180deg,#f29a3c 0%,#f6b363 22%,#8ed0e6 23%,#7cc6e0 100%)}
.play{left:311px;top:193px;width:62px;height:42px;border-radius:8px;background:rgba(20,20,20,.8)}

/* Partners */
.partners .section-title{top:2632px;text-transform:uppercase;font-size:42px}
.partner-logo{top:2716px;width:168px;height:93px;border:1px solid #999;background:var(--white);display:flex;align-items:center;justify-content:center;font-size:16px;color:#333}
.carousel-arrow{top:2749px;width:26px;height:26px;border-radius:50%;border:1px solid #bbb;background:var(--white)}

/* Footer */
.site-footer{position:absolute;left:0;top:2864px;width:1200px;height:58px;background:var(--footer);font-size:12px;color:#8a8a8a}
.footer-copy{left:80px;top:20px}
.footer-links{left:488px;top:20px}
.social{left:920px;top:13px;display:flex;gap:10px}
.social span{width:33px;height:33px;border-radius:50%;border:2px solid var(--white)}
</style>
</head>
<body>

<header class="hero">
  <div class="hero-photo" role="img" aria-label="Night city skyline with a suspension bridge reflected in the river"></div>
  <div class="abs brand"><span class="brand-name">Pelmora</span></div>
  <div class="abs menu"><span></span><span></span><span></span></div>
  <h1 class="abs hero-title">The Evolution Of Feedback</h1>
  <p class="abs hero-sub">Improve your ROI and get new ideas by collaborating with Pelmora's experts</p>
  <a class="abs btn-ghost" style="left:405px;width:179px">Post Project</a>
  <a class="abs btn-ghost" style="left:614px;width:181px">How It Works</a>
  <svg class="abs scroll-cue" width="50" height="26" viewBox="0 0 50 26"><polyline points="2,2 25,22 48,2" fill="none" stroke="#f7941d" stroke-width="2"/></svg>
</header>

<section class="how">
  <h2 class="section-title"><span class="teal">How It</span> <span class="orange">Works</span></h2>
  <p class="abs how-sub">For businesses that need actionable feedback on all types of digital and print material</p>
  <div class="abs step" style="left:83px">
    <div class="step-art" role="img" aria-label="Illustration of a clipboard with a team of people"></div>
    <p class="step-label">Post Your Project</p>
  </div>
  <div class="abs step" style="left:440px">
    <div class="step-art" role="img" aria-label="Illustration of two people collaborating over documents"></div>
    <p class="step-label">Collaborate With Our Experts</p>
  </div>
  <div class="abs step" style="left:795px">
    <div class="step-art" role="img" aria-label="Illustration of a person working at a desk with a computer"></div>
    <p class="step-label">Revise Your Material</p>
  </div>
</section>

<section class="why">
  <h2 class="abs why-title"><span class="teal">Why Do</span> <span class="orange">You Need Us</span></h2>
  <p class="abs why-copy">Crowdsource your company's content like never before with Pelmora! With thousands of experienced writers specializing in dozens of skillsets, you can transform an ecommerce product page into a conversion machine or make a newsletter extremely engaging.</p>
  <ul class="abs why-list">
    <li>Cost effective way for businesses of all sizes to perfect content before it hits their customers</li>
    <li>Bloggers and authors can boost creativity networking with the crowd</li>
    <li>Quick and easy way to get feedback from multiple writing experts on all types of content.</li>
  </ul>
  <a class="abs btn-outline">VIEW A DEMO</a>
  <div class="abs devices-art" role="img" aria-label="Laptop and phone showing the collaboration app with cartoon characters"></div>
</section>

<section class="projects" role="region" aria-label="Project types">
  <div class="proj-col" style="left:78px">
    <h3 style="width:282px">Projects Types</h3>
    <ul>
      <li>Lorem ipsum dolor sit amet, consectetur adipiscing elit.</li>
      <li>Duis non vestibulum urna, at finibus quam. Phasellus at nulla .</li>
      <li>In gravida semper est, eu aliquam nisi.</li>
      <li>Proin tempus cursus vehicula. Proin facilisis a dolor ut faucibus.</li>
      <li>Maecenas ac ligula rutrum, vehicula odio at, suscipit orci.</li>
      <li>Proin tempus cursus vehicula. Proin facilisis a dolor ut faucibus.</li>
      <li>In gravida semper est, eu aliquam nisi.</li>
    </ul>
  </div>
  <div class="proj-col" style="left:524px">
    <h3 style="width:212px">Print Projects</h3>
    <ul>
      <li>Lorem ipsum dolor sit .</li>
      <li>Lorem ipsum dolor sit amet finibus.</li>
      <li>Lorem ipsum dolor sit amet .</li>
      <li>Lorem ipsum dolor sit amet finibus.</li>
      <li>Lorem ipsum dolor sit amet.</li>
      <li>Lorem ipsum&nbsp; sit amet finibus.</li>
      <li>Lorem ipsum .</li>
    </ul>
  </div>
  <div class="proj-col" style="left:879px">
    <h3 style="width:212px">Digital Projects</h3>
    <ul>
      <li>Lorem ipsum dolor sit .</li>
      <li>Lorem ipsum dolor sit amet finibus.</li>
      <li>Lorem ipsum dolor sit amet .</li>
      <li>Lorem ipsum dolor sit amet finibus.</li>
      <li>Lorem ipsum dolor sit amet .</li>
      <li>Lorem ipsum&nbsp; sit amet finibus .</li>
      <li>Lorem ipsum .</li>
    </ul>
  </div>
</section>

<section class="what">
  <h2 class="section-title"><span class="teal">What</span> <span class="orange">We Do</span></h2>
  <p class="abs what-copy">Lorem ipsum dolor sit amet, consectetur adipiscing elit. Proin feugiat volutpat quam, sed elementum ligula placerat eleifend. Curabitur et accumsan justo, eget interdum odio.</p>
  <div class="abs tablet">
    <div class="abs tablet-screen" role="img" aria-label="Video still of a cartoon team of copywriters">
      <div class="abs play"><svg width="62" height="42" viewBox="0 0 62 42"><polygon points="26,13 26,29 38,21" fill="#fff"/></svg></div>
    </div>
  </div>
</section>

<section class="partners">
  <h2 class="section-title"><span class="teal">Our</span> <span class="orange">Partners</span></h2>
  <svg class="abs carousel-arrow" style="left:26px" viewBox="0 0 26 26"><polygon points="15,8 9,13 15,18" fill="#333"/></svg>
  <div class="abs partner-logo" style="left:80px">LOGO</div>
  <div class="abs partner-logo" style="left:298px">LOGO</div>
  <div class="abs partner-logo" style="left:516px">LOGO</div>
  <div class="abs partner-logo" style="left:734px">LOGO</div>
  <div class="abs partner-logo" style="left:953px">LOGO</div>
  <svg class="abs carousel-arrow" style="left:1146px" viewBox="0 0 26 26"><polygon points="11,8 17,13 11,18" fill="#333"/></svg>
</section>

<footer class="site-footer">
  <p class="abs footer-copy">© 2015 All rights reserved Pelmora</p>
  <p class="abs footer-links">Contact | Careers | Privacy | Terms of Use</p>
  <div class="abs social"><span></span><span></span><span></span><span></span><span></span></div>
</footer>

</body>
</html>
```